Realtor branding business card

modern, simple and self branding. Broker office logo needs to be used but not emphasized. Looking to brand myself

Target Market(s)

buyers, sellers and investors

Industry/Entity Type

Realtor

Contact Information for Business Card

Sample of my current business card on file

Requirements
Must have
• my website - tobiasmerrowkl.com
• Realtor logo
• Fair housing logo
Nice to have
• Colors from office logo but not a must
Should not have
• Do not want headshot

```html
<!DOCTYPE html>
<html lang="en">
<head>
<meta charset="utf-8">
<title>Tobias Merrow – Realtor Business Card</title>
<link rel="stylesheet" href="https://fonts.googleapis.com/css2?family=Roboto:wght@400;500;700;900&display=swap">
<style>
  :root {
    --navy: #25166c;
    --red: #d9261c;
    --white: #ffffff;
    --text-grey: #555555;
    --backdrop: #e9e7e3;
  }
  * { margin: 0; padding: 0; box-sizing: border-box; }
  html, body {
    width: 1125px;
    height: 1200px;
    overflow: hidden;
    background: var(--backdrop);
    font-family: "Roboto", Arial, sans-serif;
  }
  .canvas { position: relative; width: 1125px; height: 1200px; }

  .card {
    position: absolute;
    left: 171px;
    width: 826px;
    height: 472px;
    overflow: hidden;
    box-shadow: 0 3px 8px rgba(0,0,0,0.25);
  }
  .card--front { top: 106px; background: var(--white); }
  .card--back { top: 639px; background: var(--navy); }

  /* Front */
  .agent { position: absolute; left: 57px; top: 79px; }
  .agent__name { font-size: 30px; font-weight: 700; color: var(--navy); line-height: 1.1; }
  .agent__title { font-size: 20px; font-weight: 500; color: var(--red); margin-top: 3px; }

  .brokerage {
    position: absolute;
    right: 52px;
    top: 54px;
    text-align: right;
    color: var(--navy);
    font-weight: 900;
    line-height: 0.95;
  }
  .brokerage__name { font-size: 56px; letter-spacing: -1px; }
  .brokerage__sub { font-size: 31px; }

  .contact {
    position: absolute;
    right: 51px;
    top: 226px;
    text-align: right;
    color: var(--text-grey);
    font-size: 19px;
    line-height: 25px;
  }
  .contact__address { margin-bottom: 13px; }
  .contact__line { display: flex; justify-content: flex-end; align-items: center; gap: 10px; line-height: 26px; }
  .contact__icon { width: 18px; height: 18px; fill: var(--navy); flex: none; }

  .web-band {
    position: absolute;
    left: 0; right: 0; bottom: 0;
    height: 52px;
    background: var(--navy);
    color: var(--white);
    font-size: 18px;
    letter-spacing: 3.3px;
    text-align: right;
    padding-right: 50px;
    line-height: 52px;
  }

  /* Back */
  .badges { position: absolute; right: 44px; top: 62px; display: flex; gap: 8px; }
  .badge { width: 36px; height: 36px; background: var(--white); }
  .badge--wide { width: 58px; }

  .brand-center {
    position: absolute;
    left: 0; right: 0;
    top: 172px;
    text-align: center;
    color: var(--white);
  }
  .brand-center__name { font-size: 74px; font-weight: 900; line-height: 1; letter-spacing: -1px; }
  .brand-center__sub { font-size: 38px; font-weight: 900; line-height: 1.05; }
  .brand-center__web { font-size: 19px; letter-spacing: 4px; margin-top: 6px; }
</style>
</head>
<body>
<main class="canvas">

  <section class="card card--front" aria-label="Business card front">
    <div class="agent">
      <p class="agent__name">Tobias Merrow, PA</p>
      <p class="agent__title">Realtor</p>
    </div>

    <div class="brokerage">
      <p class="brokerage__name">Brightfield</p>
      <p class="brokerage__sub">Realty Group</p>
    </div>

    <div class="contact">
      <p class="contact__address">48 Larkspur Ave.<br>Cedar Hollow, FL 32990</p>
      <p class="contact__line">555.210.4800
        <svg class="contact__icon" viewBox="0 0 24 24" aria-hidden="true"><path d="M6.6 10.8a15.2 15.2 0 0 0 6.6 6.6l2.2-2.2a1 1 0 0 1 1-.25 11.4 11.4 0 0 0 3.6.57 1 1 0 0 1 1 1V20a1 1 0 0 1-1 1A17 17 0 0 1 3 4a1 1 0 0 1 1-1h3.5a1 1 0 0 1 1 1c0 1.25.2 2.45.57 3.57a1 1 0 0 1-.25 1z"/></svg>
      </p>
      <p class="contact__line">555.318.7264
        <svg class="contact__icon" viewBox="0 0 24 24" aria-hidden="true"><path d="M7 1h10a2 2 0 0 1 2 2v18a2 2 0 0 1-2 2H7a2 2 0 0 1-2-2V3a2 2 0 0 1 2-2zm0 3v14h10V4zm5 15.2a1.2 1.2 0 1 0 0 2.4 1.2 1.2 0 0 0 0-2.4z"/></svg>
      </p>
      <p class="contact__line">merrowhomes@mailbox.com
        <svg class="contact__icon" viewBox="0 0 24 24" aria-hidden="true"><path d="M2 5h20v14H2zm2 2v.4l8 5.2 8-5.2V7zm0 2.8V17h16V9.8l-8 5.2z"/></svg>
      </p>
    </div>

    <div class="web-band">tobiasmerrowkl.com</div>
  </section>

  <section class="card card--back" aria-label="Business card back">
    <div class="badges">
      <span class="badge" role="img" aria-label="Realtor membership badge"></span>
      <span class="badge badge--wide" role="img" aria-label="Equal housing opportunity badge"></span>
    </div>

    <div class="brand-center">
      <p class="brand-center__name">Brightfield</p>
      <p class="brand-center__sub">Realty Group</p>
      <p class="brand-center__web">tobiasmerrowkl.com</p>
    </div>
  </section>

</main>
</body>
</html>
```